International Marketing Company - Web Design Project

vRelay is a well-funded start up in London developing an Online Marketing Platform for small businesses in Europe.

We require a large number of high quality business web designs for our business website builder. Our business websites are completely integrated into our Online Marketing systems and therefore it is important for designers to comply with our Design Guidelines.

This initial contest is a trial for us to open up the design process to top designers for the Builders vertical (e.g. Builders, Electricians, Plumbers, Flooring, etc.). We have implemented a base html structure and design and included them in the files.

Use your creativity to design new and fresh designs based on the included elements (e.g. testimonials, business description, etc).

We will award the stated prize money for the top three designs.

Any designers that submit designs we feel are of a high enough quality but do not make the top 3 could still be compensated and WILL be invited to participate in our next vertical competition.

Therefore, we encourage designers to submit as many designs as possible as we may award up to 25 designs.

Submissions will be reviewed daily and feedback provided where possible.

Designers who can also code will have the options to implement their designs for an additional fee.

Good luck!
Updates

There has been a mistake made in regard to the prize. Pixel Harbor should have it fixed soon.

1st place = £350
2nd place = £250
3rd Place = £150

Thanks,
Morris
25/11/2011

UPDATE:

1st place will win £350
2nd place will win £250
3rd place will win £150

Everything else is as to the specification.

Thanks
Morris

Target Market(s)

Builders, Electricians, Plumbers, Tradesman, Small construction companies

Industry/Entity Type

Business

Requirements
Must have
• Totally new designs based around the elements we want to show on each page.

We are looking for something different to the design we already have. But you can use that as a starting point.

Use the included files to see what is required for each page. Here is a brief outline:

Homepage - Testimonials, News, Business Description, Latest Projects and Call to action

About-Us - Team Summary, About the Business and a call to action

Projects Page - Project Details (Oage Title and description), Each project needs a title, content and 2 images.

Testimonials Page - The testifiers name and their comment

Contacts Page - Terrafind Map, Company address, business hours, contact form and a call to action.

Please submit final designs in Photoshop or Fireworks format.

Each page has a set of elements. These element must feature in the design of that page. See supporting documents for page details.

All elements must be included in your design. Please do not add any extra element.

Professional look and feel
Nice to have
• Design variations:
Full width designs
Boxed Designs
With AND without carousels
OR static images
Good use of stock images.

Creative use of the elements, dont be restricted/influenced by the default design we have already

Designs based on the 960 grid

```html
<!DOCTYPE html>
<html lang="en">
<head>
<meta charset="utf-8">
<title>RB Builders – Home</title>
<link rel="stylesheet" href="https://fonts.googleapis.com/css2?family=Arimo:ital,wght@0,400;0,700;1,400&family=Noto+Sans:ital,wght@0,400;1,400&display=swap">
<style>
:root{
  --yellow:#ffd700;
  --gold:#e9c232;
  --ink:#111;
  --text:#1e1e1e;
  --muted:#6f6f6f;
  --rule:#e6e6e6;
  --side:#f8f8f8;
  --white:#fff;
}
*{box-sizing:border-box;margin:0;padding:0}
html,body{width:1200px;height:900px;overflow:hidden;background:var(--white)}
body{position:relative;font-family:"Noto Sans",Tahoma,sans-serif;color:var(--text)}
.abs{position:absolute}

.brand{left:122px;top:20px;display:flex;align-items:center;gap:8px;font-family:"Arimo",Arial,sans-serif;font-weight:700;font-size:26px;color:var(--ink)}
.brand-dot{width:14px;height:14px;border-radius:50%;background:var(--yellow)}

.navbar{left:119px;top:60px;width:961px;height:45px;background:linear-gradient(#3a3a3a,#050505)}
.nav{left:153px;top:60px;height:45px;display:flex;align-items:center;gap:16px;font-family:"Arimo",Arial,sans-serif;font-size:18px;color:var(--white);list-style:none}
.call{left:802px;top:60px;width:278px;height:45px;background:linear-gradient(#ffe033,#ffd000);display:flex;align-items:center;padding-left:13px;gap:11px;font-family:"Arimo",Arial,sans-serif;font-size:20px;color:#222}
.call-icon{width:24px;height:24px;background:#222;border-radius:3px;display:flex;align-items:center;justify-content:center}

.hero{left:120px;top:105px;width:960px;height:267px;background:linear-gradient(100deg,#e9d3b8 0%,#c89a6c 30%,#8a8a92 48%,#b27a4a 70%,#d9b48a 100%)}
.hero-panel{left:665px;top:202px;width:415px;height:170px;background:rgba(70,55,45,.72)}
.hero-title{right:176px;top:243px;font-family:"Arimo",Arial,sans-serif;font-style:italic;font-size:50px;color:var(--white);text-align:right;white-space:nowrap;letter-spacing:-1px}
.hero-tag{right:180px;top:300px;font-family:"Arimo",Arial,sans-serif;font-size:38px;color:var(--white);white-space:nowrap;letter-spacing:-.5px}

.section-title{font-family:"Arimo",Arial,sans-serif;font-weight:700;font-size:20px;color:var(--ink);letter-spacing:-.3px}
.section-title span{color:var(--gold)}
.welcome-title{left:120px;top:382px}
.welcome-rule{left:120px;top:405px;width:358px;height:5px;background:var(--ink)}
.intro{left:120px;top:417px;width:690px;font-size:11.7px;line-height:14.5px;letter-spacing:-.15px}
.intro p{margin-bottom:14.5px}

.projects-title{left:123px;top:573px}
.projects-rule{left:123px;top:596px;width:358px;height:5px;background:var(--yellow)}
.project{top:614px;width:207px}
.project-frame{height:156px;border:1px solid #d9d9d9;background:#f4f4f4;padding:5px}
.project-photo{width:100%;height:100%;background:linear-gradient(160deg,#e8e6e2 0%,#c9a777 45%,#b98e5a 60%,#d9d6cf 100%)}
.project-shadow{margin:0 auto;width:196px;height:9px;background:radial-gradient(ellipse at top,rgba(0,0,0,.45),rgba(0,0,0,0) 70%)}
.project-caption{margin-top:8px;text-align:center;font-size:14px;color:var(--muted)}

.sidebar{left:821px;top:372px;width:259px;height:448px;background:var(--side)}
.cta{left:854px;top:394px;width:175px;height:86px;background:linear-gradient(#3b3b3b,#0b0b0b);text-align:center;font-family:"Arimo",Arial,sans-serif;font-weight:700;color:var(--yellow);overflow:hidden}
.cta-big{font-size:25px;margin-top:6px}
.cta-small{font-size:14px;line-height:17px;margin-top:2px}
.cta svg{position:absolute;right:0;bottom:0}
.side-title{font-family:"Arimo",Arial,sans-serif;font-weight:700;font-size:19px;color:var(--ink);letter-spacing:-.4px}
.side-title span{color:var(--gold)}
.side-rule{height:5px;width:200px;background:var(--ink)}
.news-title{left:836px;top:499px}
.news-rule{left:836px;top:523px}
.news-item{left:838px;top:538px;width:215px;font-size:12.5px;line-height:15.5px;color:#444;padding-left:14px;letter-spacing:-.1px}
.news-item::before{content:"»";position:absolute;left:0;top:0;color:#777}
.news-sep{left:838px;top:578px;width:210px;height:1px;background:#e0e0e0}
.say-title{left:838px;top:597px}
.say-rule{left:838px;top:620px}
.quote{left:853px;top:651px;width:212px;font-style:italic;font-size:12.3px;line-height:15.5px;color:#555;text-indent:36px;letter-spacing:-.3px}
.qmark{font-family:Georgia,serif;font-size:44px;color:#cfcfcf;line-height:1}
.q-open{left:853px;top:633px}
.q-close{left:1040px;top:748px}
.quote-by{left:853px;top:778px;font-size:12.5px;color:#666}
.more{left:994px;top:779px;font-size:12.5px;color:var(--gold)}
.say-sep{left:844px;top:809px;width:211px;height:1px;background:#e0e0e0}

.footer-rule{left:120px;top:852px;width:960px;height:5px;background:var(--rule)}
.footer-nav{left:120px;top:865px;font-size:12px;color:#555}
.copyright{right:120px;top:866px;font-size:12px;color:#555}
</style>
</head>
<body>

<header>
  <div class="abs brand"><span class="brand-dot"></span>RB Builders</div>
  <div class="abs navbar"></div>
  <ul class="abs nav"><li>Home</li><li>About</li><li>Testimonials</li><li>Portfolio</li><li>Contacts</li></ul>
  <div class="abs call">
    <span class="call-icon"><svg width="14" height="16" viewBox="0 0 14 16"><path d="M3 1h3l1 4-2 1c1 2 2 4 4 5l1-2 4 1v3c0 1-1 2-2 2C6 15 0 9 1 3c0-1 1-2 2-2z" fill="#ffd700"/></svg></span>
    <span>Call : 020. 7946 0321</span>
  </div>
</header>

<section>
  <div class="abs hero" role="img" aria-label="Photo of a builder in a hard hat working in a timber-framed house"></div>
  <div class="abs hero-panel"></div>
  <div class="abs hero-title">RB BUILDERS</div>
  <div class="abs hero-tag">Quick . Solid . Quality</div>
</section>

<main>
  <h1 class="abs section-title welcome-title">Welcome to <span>RB</span> Builders</h1>
  <div class="abs welcome-rule"></div>
  <div class="abs intro">
    <p>I am an experienced builder in Crawley, RB Construction have been based in Crawley for over 10 years. My team and I are proven, reliable builders based in Crawley. We've come across a lot in our time, so don't hesitate to get in touch about any building job in Crawley.</p>
    <p>I am a friendly, handyman who has built a team of excellent tradesmen based in Crawley. My builders in Crawley have years of experience in kitchen renovation, bathroom renovation, roofing and plumbing, loft conversions and house restoration.</p>
    <p>Call RB Construction on 0209460321 now to discuss how we can help you. My quotes are always FREE with no obligation.</p>
  </div>

  <h2 class="abs section-title projects-title">Latest Projects</h2>
  <div class="abs projects-rule"></div>
  <div class="abs project" style="left:122px">
    <div class="project-frame"><div class="project-photo" role="img" aria-label="Photo of a renovated kitchen with wooden cabinets"></div></div>
    <div class="project-shadow"></div>
    <div class="project-caption">House restoration in Crawley</div>
  </div>
  <div class="abs project" style="left:361px">
    <div class="project-frame"><div class="project-photo" role="img" aria-label="Photo of a renovated kitchen with wooden cabinets"></div></div>
    <div class="project-shadow"></div>
    <div class="project-caption">House restoration in Crawley</div>
  </div>
  <div class="abs project" style="left:600px">
    <div class="project-frame"><div class="project-photo" role="img" aria-label="Photo of a renovated kitchen with wooden cabinets"></div></div>
    <div class="project-shadow"></div>
    <div class="project-caption">House restoration in Crawley</div>
  </div>
</main>

<aside>
  <div class="abs sidebar"></div>
  <div class="abs cta">
    <div class="cta-big">Contact Us</div>
    <div class="cta-small">For a<br>QUOTE NOW!</div>
    <svg width="40" height="30" viewBox="0 0 40 30"><rect x="1" y="1" width="38" height="28" fill="none" stroke="#555" stroke-width="1.5"/><path d="M1 1l19 15L39 1" fill="none" stroke="#555" stroke-width="1.5"/></svg>
  </div>

  <h3 class="abs side-title news-title">Latest<span>News</span></h3>
  <div class="abs side-rule news-rule"></div>
  <div class="abs news-item">RB Construction have just finished another fine job in Crawley.</div>
  <div class="abs news-sep"></div>

  <h3 class="abs side-title say-title">Customers<span>Say</span></h3>
  <div class="abs side-rule say-rule"></div>
  <div class="abs qmark q-open">“</div>
  <p class="abs quote">I found RB Construction in Crawley through their amazing website and I made my decision to ask for a quote once I saw the excellent testimonials. It can be very difficult to find great builders in Crawley but RB Construction's team delivers</p>
  <div class="abs qmark q-close">”</div>
  <div class="abs quote-by">- Mr. Hallworth</div>
  <div class="abs more">+ more</div>
  <div class="abs say-sep"></div>
</aside>

<footer>
  <div class="abs footer-rule"></div>
  <div class="abs footer-nav">Home | About Us | Testimonials | Portfolio | Contact</div>
  <div class="abs copyright">© Copyright 2011 - RB Builders</div>
</footer>

</body>
</html>
```